Modern Verdell Tree Care Website

I need a website for a full service Tree Care company. The company provides tree pruning, tree removal, tree preservation, emergency services, stump grinding, and emergency tree services.

Target Market(s)

Customers that need tree services

Industry/Entity Type

Landscaping, Tree Services

Coding

Coded - Design and coding required

Number of Pages Required

5+ page

Font styles to use
Sans Serif

Requirements
Must have
• Good clean design that showcases the services the company provides.
Nice to have
• Services page; contact form, blog, home page, about page

```html
<!DOCTYPE html>
<html lang="en">
<head>
<meta charset="utf-8">
<title>Verdell Tree Care</title>
<link href="https://fonts.googleapis.com/css2?family=Syncopate:wght@400;700&family=Montserrat:wght@400;500;600;700&display=swap" rel="stylesheet">
<style>
:root{
  --green:#7cb83a;
  --green-dark:#5f9a26;
  --field:#6aa92c;
  --orange:#e8a23a;
  --orange-soft:#f1b04a;
  --ink:#1f1f1f;
  --text:#4a4a4a;
  --footer:#2c2c2c;
  --white:#ffffff;
}
*{box-sizing:border-box;margin:0;padding:0}
html,body{width:1200px;height:3871px;overflow:hidden}
body{font-family:'Montserrat',sans-serif;color:var(--text);background:var(--white);position:relative}
.display{font-family:'Syncopate',sans-serif;font-weight:700;text-transform:uppercase;color:var(--ink);letter-spacing:1px}
a{text-decoration:none;color:inherit}
.abs{position:absolute}

/* hero */
.hero{position:absolute;left:0;top:0;width:1200px;height:640px;background:radial-gradient(circle at 60% 55%,#8fa34a 0%,#4f6d2a 40%,#2d4418 75%,#1e2f10 100%)}
.nav{position:absolute;left:16px;top:33px;width:1166px;height:84px;background:var(--white);border-radius:42px;display:flex;align-items:center;padding:0 34px 0 32px}
.brand{display:flex;align-items:center;gap:10px;width:210px}
.brand-dot{width:28px;height:28px;background:var(--orange)}
.brand-name{font-weight:700;font-size:17px;color:var(--green-dark);line-height:1.1;letter-spacing:1px}
.menu{display:flex;gap:55px;margin-left:40px;font-size:13.5px;font-weight:500;color:#222}
.nav-phone{margin-left:auto;display:flex;align-items:center;gap:6px;font-weight:600;font-size:15px;color:#222}
.btn-nav{margin-left:20px;background:var(--green);color:var(--white);font-weight:600;font-size:15px;border-radius:24px;padding:13px 22px}
.hero-copy{position:absolute;left:0;top:212px;width:1200px;text-align:center;color:var(--white)}
.hero-copy .welcome{font-family:'Syncopate',sans-serif;font-size:33px;letter-spacing:2px;color:var(--white)}
.hero-copy h1{font-family:'Syncopate',sans-serif;font-weight:700;font-size:56px;letter-spacing:2px;margin-top:4px}
.hero-copy p{font-size:19px;line-height:34px;font-weight:500;margin-top:12px}
.btn-hero{display:inline-block;margin-top:24px;background:var(--white);color:var(--orange);font-weight:600;font-size:16px;padding:13px 28px;border-radius:24px}

/* about */
.about-photo{left:108px;top:748px;width:468px;height:460px;background:linear-gradient(135deg,#6f7a52,#3f4d2a 60%,#4b5f2f)}
.about-text{left:632px;top:762px;width:420px}
.about-text h2{font-size:38px;line-height:52px}
.about-text p{font-size:14.5px;line-height:30px;margin-top:24px}
.btn{display:inline-block;background:var(--orange-soft);color:var(--white);font-weight:700;font-size:14px;border-radius:26px;text-align:center}
.about-text .btn{margin-top:22px;width:172px;padding:15px 0}

/* services */
.services{left:0;top:1318px;width:1200px;height:688px;background:linear-gradient(180deg,#82bd3f,#76b236)}
.services-intro{left:110px;top:1430px;width:260px}
.services-intro h2{font-size:38px;line-height:52px;color:#1b1b1b}
.services-intro p{font-size:19px;line-height:38px;color:#2d3a18;margin-top:24px}
.services-intro .btn{margin-top:18px;width:170px;padding:15px 0}
.card{position:absolute;top:1437px;width:252px;height:419px;background:var(--orange);border:2px solid #f4c071;border-radius:4px;padding:4px}
.card-photo{width:100%;height:200px;border-radius:2px}
.card h3{font-size:19px;font-weight:700;color:var(--white);margin:22px 12px 0;line-height:34px}
.card p{font-size:14px;line-height:32px;color:var(--white);margin:6px 16px 0}
.card .more{display:block;font-size:12.5px;font-weight:700;color:var(--white);margin:12px 20px 0}
.dots{left:520px;top:1906px;display:flex;gap:12px}
.dots span{width:44px;height:5px;background:var(--white);border-radius:3px}
.dots span:first-child{background:var(--orange)}

/* blog */
.blog-title{left:0;top:2096px;width:1200px;text-align:center;font-size:40px}
.post-lg{left:105px;top:2180px;width:480px;height:395px;border:1.5px solid #f2c27d;border-radius:6px;background:var(--white);box-shadow:0 2px 8px rgba(0,0,0,.08);padding:6px}
.post-lg .ph{height:180px;border-radius:4px;background:linear-gradient(135deg,#3d4a2e,#6b6a3c 50%,#2f3b22)}
.post-lg h3{font-size:19px;font-weight:500;color:#111;line-height:32px;margin:12px 10px 0}
.date{display:flex;align-items:center;gap:8px;font-size:12.5px;font-weight:600;color:var(--orange);margin-top:8px}
.post-lg .date{margin-left:12px;margin-top:12px}
.post-lg p{font-size:14px;line-height:27px;margin:10px 12px 0}
.readmore{display:block;font-size:14px;font-weight:600;color:var(--orange);text-decoration:underline}
.post-lg .readmore{margin:3px 12px 0}
.post-sm{position:absolute;left:601px;width:481px;height:184px;border:1.5px solid #f2c27d;border-radius:6px;background:var(--white);box-shadow:0 2px 8px rgba(0,0,0,.08);padding:4px;display:flex}
.post-sm .ph{width:208px;height:174px;border-radius:3px;flex:none}
.post-sm .body{padding:8px 10px 0 12px}
.post-sm h4{font-size:14.5px;font-weight:500;color:#111;line-height:27px}
.post-sm .date{margin-top:2px;margin-left:4px}
.post-sm p{font-size:13px;line-height:27px;margin:4px 0 0 4px}
.post-sm .readmore{margin:3px 0 0 4px}
.blog .btn{left:511px;top:2633px;width:169px;padding:15px 0;position:absolute}

/* contact */
.contact{left:0;top:2760px;width:1200px;height:687px;background:linear-gradient(90deg,#3d4e25 0%,#556a30 35%,#6b6a36 65%,#4d4a26 100%)}
.contact h2{position:absolute;left:120px;top:2822px;font-size:40px;color:var(--white)}
.label{position:absolute;font-size:14.5px;font-weight:500;color:var(--white)}
.field{position:absolute;height:51px;width:248px;background:var(--field);border-radius:22px;display:flex;align-items:center;justify-content:flex-end;padding-right:16px}
.field.msg{height:124px;width:507px;align-items:flex-start;padding-top:18px}
.btn-submit{position:absolute;left:114px;top:3290px;width:156px;height:46px;background:var(--white);border-radius:23px;color:var(--orange);font-size:14.5px;display:flex;align-items:center;justify-content:center}

/* footer */
.footer{left:0;top:3447px;width:1200px;height:424px;background:var(--footer);color:var(--white)}
.foot-brand{position:absolute;left:108px;top:3538px;width:196px;height:117px;background:var(--white);border-radius:3px;display:flex;align-items:center;justify-content:center;gap:10px}
.foot-col{position:absolute;top:3532px}
.foot-col h5{font-size:20px;font-weight:500;letter-spacing:.5px}
.foot-col ul{list-style:none;margin-top:18px}
.foot-col li{font-size:15.5px;line-height:32px}
.contact-list{margin-top:18px;font-size:14px;line-height:28px}
.contact-list .k{display:flex;align-items:center;gap:8px;font-weight:600}
.contact-list .v{padding-left:22px}
.foot-rule{position:absolute;left:111px;top:3815px;width:978px;height:1px;background:#bdbdbd}
.copy{position:absolute;left:0;top:3834px;width:1200px;text-align:center;font-size:13.5px;color:var(--white)}
</style>
</head>
<body>

<section class="hero" role="img" aria-label="Photo of cupped hands holding a young seedling in soil, green blurred forest background"></section>
<header class="nav">
  <div class="brand"><span class="brand-dot"></span><span class="brand-name">VERDELL<br>TREE CARE</span></div>
  <nav class="menu"><a>HOME</a><a>ABOUT US</a><a>SERVICES</a><a>BLOG</a><a>CONTACT</a></nav>
  <div class="nav-phone">
    <svg width="18" height="18" viewBox="0 0 24 24"><path fill="#e0284a" d="M6.6 10.8a15 15 0 0 0 6.6 6.6l2.2-2.2a1 1 0 0 1 1-.25 11.4 11.4 0 0 0 3.6.57 1 1 0 0 1 1 1V20a1 1 0 0 1-1 1A17 17 0 0 1 3 4a1 1 0 0 1 1-1h3.5a1 1 0 0 1 1 1c0 1.25.2 2.45.57 3.57a1 1 0 0 1-.25 1z"/></svg>
    +1 555 014 2290
  </div>
  <a class="btn-nav">Get In Touch</a>
</header>
<div class="hero-copy">
  <div class="welcome">WELCOME TO</div>
  <h1>VERDELL TREE CARE</h1>
  <p>Lorem Ipsum is simply dummy text of the printing and<br>typesetting industry. Lorem Ipsum has been the industry's</p>
  <a class="btn-hero">Get Started</a>
</div>

<div class="abs about-photo" role="img" aria-label="Photo of a gardener in a cap and gloves planting seedlings"></div>
<div class="abs about-text">
  <h2 class="display">About<br>Verdell Tree Care</h2>
  <p>Lorem Ipsum is simply dummy text of the printing and typesetting industry. Lorem Ipsum has been the industry's standard dummy text ever since the 1500s, when an unknown printer took a galley of type and scrambled it to make a type specimen book. It has survived not only five centuries, but also the leap into electronic typesetting, remaining essentially unchanged</p>
  <a class="btn">READ MORE</a>
</div>

<section class="abs services" role="img" aria-label="Green tinted forest texture background"></section>
<div class="abs services-intro">
  <h2 class="display">Our<br>Services</h2>
  <p>Tree Pruning, Tree Removal, Tree Preservation, Emergency Services, Stump Grinding, And Emergency Tree</p>
  <a class="btn">READ MORE</a>
</div>
<article class="card" style="left:393px">
  <div class="card-photo" role="img" aria-label="Photo of pruning shears cutting a branch" style="background:linear-gradient(135deg,#8ea54c,#5c6b3a)"></div>
  <h3>Tree Pruning</h3>
  <p>Lorem Ipsum is simply dummy text of the printing and typesetting industry.</p>
  <a class="more">READ MORE</a>
</article>
<article class="card" style="left:664px">
  <div class="card-photo" role="img" aria-label="Photo of an arborist climbing a tall tree trunk" style="background:linear-gradient(135deg,#9bb07a,#4e6a38)"></div>
  <h3>Tree Removal</h3>
  <p>Lorem Ipsum is simply dummy text of the printing and typesetting industry.</p>
  <a class="more">READ MORE</a>
</article>
<article class="card" style="left:938px">
  <div class="card-photo" role="img" aria-label="Photo of hands holding soil with a sprout growing from coins" style="background:linear-gradient(135deg,#3a3a2a,#6f5a3a 60%,#2a2a20)"></div>
  <h3>Emergency Tree Services</h3>
  <p>Lorem Ipsum is simply dummy text of the printing</p>
  <a class="more">READ MORE</a>
</article>
<div class="abs dots"><span></span><span></span><span></span></div>

<section class="blog">
  <h2 class="abs display blog-title">Our Blog</h2>
  <article class="abs post-lg">
    <div class="ph" role="img" aria-label="Photo of volunteers planting seedlings in a row"></div>
    <h3>Lorem Ipsum is simply dummy text of the printing and typesetting industry. Lorem</h3>
    <div class="date"><svg width="14" height="14" viewBox="0 0 24 24" fill="none" stroke="#e8a23a" stroke-width="2"><rect x="3" y="5" width="18" height="16" rx="2"/><path d="M3 10h18M8 3v4M16 3v4"/></svg>Feb 26, 2024</div>
    <p>Lorem Ipsum is simply dummy text of the printing and typesetting industry. Lorem Ipsum Lorem Ipsum is simply</p>
    <a class="readmore">Read More...</a>
  </article>
  <article class="post-sm" style="top:2183px">
    <div class="ph" role="img" aria-label="Photo of hands planting small seedlings in dark soil" style="background:linear-gradient(135deg,#3b3327,#5d5a3a)"></div>
    <div class="body">
      <h4>Lorem Ipsum is simply dummy text of the printing</h4>
      <div class="date"><svg width="14" height="14" viewBox="0 0 24 24" fill="none" stroke="#e8a23a" stroke-width="2"><rect x="3" y="5" width="18" height="16" rx="2"/><path d="M3 10h18M8 3v4M16 3v4"/></svg>Dec 01, 2020</div>
      <p>Lorem Ipsum is simply dummy text of the printing and typesetting</p>
      <a class="readmore">Read More...</a>
    </div>
  </article>
  <article class="post-sm" style="top:2385px">
    <div class="ph" role="img" aria-label="Photo of a hand placing a sapling into brown earth" style="background:linear-gradient(135deg,#4a3424,#8a5a38)"></div>
    <div class="body">
      <h4>Lorem Ipsum is simply dummy text of the printing</h4>
      <div class="date"><svg width="14" height="14" viewBox="0 0 24 24" fill="none" stroke="#e8a23a" stroke-width="2"><rect x="3" y="5" width="18" height="16" rx="2"/><path d="M3 10h18M8 3v4M16 3v4"/></svg>Feb 26, 2024</div>
      <p>Lorem Ipsum is simply dummy text of the printing and</p>
      <a class="readmore">Read More...</a>
    </div>
  </article>
  <a class="btn">LEARN MORE</a>
</section>

<section class="abs contact" role="img" aria-label="Photo of a worker in a cap planting a young tree in a field"></section>
<h2 class="display" style="position:absolute;left:120px;top:2822px;font-size:40px;color:#fff">Contact Us</h2>
<span class="label" style="left:126px;top:2904px">Name</span>
<span class="label" style="left:408px;top:2904px">Contact Number</span>
<div class="field" style="left:111px;top:2935px"><svg width="16" height="16" viewBox="0 0 24 24" fill="#fff"><circle cx="12" cy="7" r="5"/><path d="M2 23c0-6 4.5-9 10-9s10 3 10 9z"/></svg></div>
<div class="field" style="left:370px;top:2935px"><svg width="16" height="16" viewBox="0 0 24 24" fill="#fff"><path d="M6.6 10.8a15 15 0 0 0 6.6 6.6l2.2-2.2a1 1 0 0 1 1-.25 11.4 11.4 0 0 0 3.6.57 1 1 0 0 1 1 1V20a1 1 0 0 1-1 1A17 17 0 0 1 3 4a1 1 0 0 1 1-1h3.5a1 1 0 0 1 1 1c0 1.25.2 2.45.57 3.57a1 1 0 0 1-.25 1z"/></svg></div>
<span class="label" style="left:130px;top:3002px">Mail Address</span>
<span class="label" style="left:412px;top:3002px">Location</span>
<div class="field" style="left:111px;top:3031px"><svg width="20" height="16" viewBox="0 0 24 18" fill="none" stroke="#fff" stroke-width="2"><rect x="1" y="1" width="22" height="16" rx="1"/><path d="M1 1l11 9 11-9"/></svg></div>
<div class="field" style="left:370px;top:3031px"><svg width="16" height="20" viewBox="0 0 24 30" fill="#fff"><path d="M12 0a11 11 0 0 0-11 11c0 8 11 19 11 19s11-11 11-19A11 11 0 0 0 12 0zm0 16a5 5 0 1 1 0-10 5 5 0 0 1 0 10z"/></svg></div>
<span class="label" style="left:130px;top:3101px">Your Message</span>
<div class="field msg" style="left:111px;top:3130px"><svg width="18" height="18" viewBox="0 0 24 24" fill="#fff"><path d="M12 2C6 2 2 6 2 11c0 2.5 1 4.6 2.8 6.2L4 22l5-2.3c1 .3 2 .4 3 .4 6 0 10-4 10-9S18 2 12 2z"/><circle cx="8" cy="11" r="1.3" fill="#6aa92c"/><circle cx="12" cy="11" r="1.3" fill="#6aa92c"/><circle cx="16" cy="11" r="1.3" fill="#6aa92c"/></svg></div>
<a class="btn-submit">SUBMIT</a>

<footer class="abs footer"></footer>
<div class="foot-brand"><span class="brand-dot"></span><span class="brand-name">VERDELL<br>TREE CARE</span></div>
<div class="foot-col" style="left:371px;color:#fff">
  <h5>INFORMATION</h5>
  <ul><li>Home</li><li>About Us</li><li>Services</li><li>Blog</li><li>Contact</li></ul>
</div>
<div class="foot-col" style="left:613px;color:#fff">
  <h5>OTHER LINKS</h5>
  <ul><li>Terms of Service</li><li>Privacy Policy</li></ul>
</div>
<div class="foot-col" style="left:887px;color:#fff">
  <h5>CONTACT</h5>
  <div class="contact-list">
    <div class="k"><svg width="13" height="13" viewBox="0 0 24 24" fill="#fff"><path d="M6.6 10.8a15 15 0 0 0 6.6 6.6l2.2-2.2a1 1 0 0 1 1-.25 11.4 11.4 0 0 0 3.6.57 1 1 0 0 1 1 1V20a1 1 0 0 1-1 1A17 17 0 0 1 3 4a1 1 0 0 1 1-1h3.5a1 1 0 0 1 1 1c0 1.25.2 2.45.57 3.57a1 1 0 0 1-.25 1z"/></svg>Call Us</div>
    <div class="v">+1 555 014 2290</div>
    <div class="k"><svg width="14" height="11" viewBox="0 0 24 18" fill="none" stroke="#fff" stroke-width="2.5"><rect x="1" y="1" width="22" height="16"/><path d="M1 1l11 9 11-9"/></svg>Mail Us</div>
    <div class="v">info@verdelltree.com</div>
    <div class="k"><svg width="12" height="15" viewBox="0 0 24 30" fill="#fff"><path d="M12 0a11 11 0 0 0-11 11c0 8 11 19 11 19s11-11 11-19A11 11 0 0 0 12 0zm0 16a5 5 0 1 1 0-10 5 5 0 0 1 0 10z"/></svg>Location</div>
    <div class="v">Lorem Ipsum Lorem<br>Ipsum Lorem</div>
  </div>
</div>
<div class="foot-rule"></div>
<div class="copy">© 2024 Verdell Tree Care I All Rights Reserved</div>

</body>
</html>
```